Business card for Eyelash extension salon in Larkmont Hills,California USA

We need new business card for our salon in Larkmont Hills. The salon name is 'Lashvera' . We would like to have...Business name: Lashvera Name of person: will provide later Address 4720 N.Alder Crest Ave Larkmont Hills , CA 90417 Phone: will provide later (Text only) Web: www.lashverastudio.example Snapgrid icon, Circlebook icon follow us for seasonal campaign and news @lashverastudiolounge Design should look elegant, high-end, clean, simple, cohesive with my brand. Please refer my brand board. Business name color will be metallic bronzy color. Im thinking grey background or white background. Thanks

Target Market(s)

25-35. Gender neutral. People who are in Entertainment business industry.
This is High-end Eyelash extension salon in Larkmont Hills

Industry/Entity Type

Beauty Salon

Contact Information for Business Card

Business name: Lashvera
Name of person: will provide later
Address 4720 N.Alder Crest Ave Larkmont Hills , CA 90417
Phone: will provide later (Text only)
Web: www.lashverastudio.example
Snapgrid icon, Circlebook icon
follow us for seasonal campaign and news @lashverastudiolounge

Requirements
Must have
• Beautiful, elegant, clean and simple look but very attractive and modern
Should not have
• We don't like too clutter, too busy designs.

```html
<!DOCTYPE html>
<html lang="en">
<head>
<meta charset="utf-8">
<title>Lashvera Business Card</title>
<link rel="stylesheet" href="https://fonts.googleapis.com/css2?family=EB+Garamond:ital,wght@0,400;0,600;1,400&family=Cormorant+Garamond:wght@400&family=Josefin+Sans:wght@400&display=swap">
<style>
  :root {
    --page: #f1ebe6;
    --card: #84634b;
    --ink: #ffffff;
    --shadow: rgba(60, 40, 25, 0.18);
  }
  * { margin: 0; padding: 0; box-sizing: border-box; }
  html, body {
    width: 1200px; height: 800px; overflow: hidden;
    background: var(--page);
  }
  .stage { position: relative; width: 1200px; height: 800px; }
  .card {
    position: absolute;
    width: 530px; height: 305px;
    background: var(--card);
    color: var(--ink);
    box-shadow: 0 6px 14px var(--shadow);
  }
  .card--front { left: 210px; top: 95px; }
  .card--back  { left: 470px; top: 410px; }

  /* front */
  .brand {
    position: absolute; left: 0; right: 0; top: 92px;
    text-align: center;
  }
  .brand__name {
    font-family: "Cormorant Garamond", serif;
    font-weight: 400;
    font-size: 84px;
    line-height: 1;
    letter-spacing: 1px;
  }
  .brand__place {
    font-family: "Josefin Sans", sans-serif;
    font-size: 10px;
    letter-spacing: 2.5px;
    margin-top: 10px;
    padding-left: 110px;
  }

  /* back */
  .contact {
    position: absolute; left: 0; right: 0; top: 70px;
    text-align: center;
    font-family: "EB Garamond", serif;
  }
  .contact__person {
    display: flex; justify-content: center; align-items: baseline; gap: 12px;
  }
  .contact__name { font-style: italic; font-size: 16px; }
  .contact__role { font-size: 10px; }
  .rule {
    width: 345px; height: 2px; background: var(--ink);
    margin: 5px auto 8px;
  }
  .contact__lines { font-size: 10.5px; line-height: 1.6; }
  .contact__label { text-decoration: underline; font-weight: 600; }
  .contact__sep { margin: 0 6px; }
  .contact__address { font-weight: 600; font-size: 11.5px; }

  .social {
    position: absolute; left: 0; right: 0; top: 214px;
    text-align: center;
    font-family: "EB Garamond", serif;
    font-size: 10.5px;
  }
  .social__invite { font-style: italic; text-decoration: underline; }
  .social__row {
    display: flex; justify-content: center; align-items: center; gap: 7px;
    margin-top: 6px;
  }
  .social__dot {
    width: 9px; height: 9px; border-radius: 50%; background: var(--ink);
  }

  .site {
    position: absolute; left: 0; right: 0; bottom: 24px;
    display: flex; justify-content: center; align-items: center; gap: 8px;
    font-family: "EB Garamond", serif;
    font-size: 10.5px; letter-spacing: 2.4px;
  }
  .site__line { width: 60px; height: 2px; background: var(--ink); }
</style>
</head>
<body>
<main class="stage">
  <section class="card card--front" aria-label="Card front">
    <div class="brand">
      <div class="brand__name">Lashvera</div>
      <div class="brand__place">LARKMONT HILLS</div>
    </div>
  </section>

  <section class="card card--back" aria-label="Card back">
    <div class="contact">
      <div class="contact__person">
        <span class="contact__name">Marisol Tennant</span>
        <span class="contact__role">Owner / Founder</span>
      </div>
      <div class="rule"></div>
      <div class="contact__lines">
        <div><span class="contact__label">Tel:</span> (+310)555-0147(Text Only)<span class="contact__sep">|</span><span class="contact__label">Email:</span> marisol@lashverastudio.example</div>
        <div class="contact__address">4720 N.Alder Crest Ave Larkmont Hills , CA 90417</div>
      </div>
    </div>

    <div class="social">
      <div class="social__invite">Follow us for seasonal campaign and news:</div>
      <div class="social__row">
        <span class="social__dot"></span>
        <span>Snapgrid · Circlebook</span>
        <span>@lashverastudiolounge</span>
      </div>
    </div>

    <div class="site">
      <span class="site__line"></span>
      <span>www.lashverastudio.example</span>
      <span class="site__line"></span>
    </div>
  </section>
</main>
</body>
</html>
```